gutter trailer wrap

I want to wrap my trailer for my gutter business. I want it to be flashy and have " seamless gutter and phone number very prominently displayed. My logo can be smaller on the wrap

I want also included " Licensed and Insured "

We install seamless gutters

Target Market(s)

home owners

Industry/Entity Type

Rain gutters - Seamless gutters

Colors
0054AA
0677BA
7BADD7
CADEEF
E8F1F8
59FF00
82FF00
B8FF75
E3FFCB
F4FFEA

Requirements
Must have
• vibrant colors

```html
<!DOCTYPE html>
<html lang="en">
<head>
<meta charset="utf-8">
<title>Seamless Gutter Installation – Trailer Wrap</title>
<link rel="stylesheet" href="https://fonts.googleapis.com/css2?family=Orbitron:wght@900&family=Lexend+Zetta:wght@200&family=Lexend:wght@300&family=Exo+2:wght@500&family=Montserrat:wght@800&display=swap">
<style>
  :root {
    --paper: #ffffff;
    --ink: #111111;
    --brand-red: #e2232a;
    --sun-yellow: #ffe619;
    --amber: #f29100;
    --flame: #e12b2b;
    --sky: #0aa0e0;
    --dusk-red: #c0504a;
    --dusk-plum: #7a3556;
    --night: #3b2560;
  }
  html, body {
    margin: 0;
    padding: 0;
    width: 1200px;
    height: 366px;
    overflow: hidden;
    background: var(--paper);
  }
  .wrap-banner {
    display: block;
    width: 1200px;
    height: 366px;
  }
  .brand-mark { fill: var(--brand-red); }
  .brand-name {
    font-family: "Montserrat", sans-serif;
    font-weight: 800;
    fill: var(--brand-red);
  }
  .headline {
    font-family: "Lexend Zetta", sans-serif;
    font-weight: 200;
    fill: var(--ink);
  }
  .subheadline {
    font-family: "Lexend", sans-serif;
    font-weight: 300;
    fill: var(--ink);
  }
  .phone {
    font-family: "Orbitron", sans-serif;
    font-weight: 900;
    fill: var(--ink);
  }
  .credentials {
    font-family: "Exo 2", sans-serif;
    font-weight: 500;
    fill: var(--brand-red);
  }
</style>
</head>
<body>
<svg class="wrap-banner" viewBox="0 0 2576 786" preserveAspectRatio="none" xmlns="http://www.w3.org/2000/svg">
  <defs>
    <linearGradient id="swoosh-tones" x1="0" y1="786" x2="2576" y2="0" gradientUnits="userSpaceOnUse">
      <stop offset="0" stop-color="var(--dusk-red)"/>
      <stop offset="0.3" stop-color="var(--flame)"/>
      <stop offset="0.5" stop-color="var(--dusk-plum)"/>
      <stop offset="0.7" stop-color="var(--night)"/>
      <stop offset="0.85" stop-color="var(--sky)"/>
      <stop offset="1" stop-color="var(--sun-yellow)"/>
    </linearGradient>
  </defs>

  <g class="swoosh-area" role="img" aria-label="Flowing decorative swoosh in red, amber, yellow, sky blue and violet">
    <path fill="url(#swoosh-tones)" d="M0 520 C80 548 150 570 220 590 C800 660 1600 560 2130 0 L2576 0 L2576 786 L0 786 Z"/>
  </g>

  <g class="brand">
    <rect class="brand-mark" x="680" y="96" width="46" height="46"/>
    <text class="brand-name" x="703" y="207" font-size="38" text-anchor="middle" textLength="240" lengthAdjust="spacingAndGlyphs">HARTWELL</text>
    <text class="brand-name" x="703" y="223" font-size="14" text-anchor="middle" textLength="240" lengthAdjust="spacingAndGlyphs">CONSTRUCTION &amp; ROOFING</text>
  </g>

  <text class="headline" x="155" y="329" font-size="86" textLength="1070" lengthAdjust="spacingAndGlyphs">SEAMLESS GUTTER</text>
  <text class="subheadline" x="580" y="365" font-size="34" textLength="250" lengthAdjust="spacingAndGlyphs">INSTALATION</text>
  <text class="phone" x="235" y="467" font-size="82" textLength="935" lengthAdjust="spacingAndGlyphs">+1-888-555-0199</text>
  <text class="credentials" x="410" y="533" font-size="52" textLength="587" lengthAdjust="spacingAndGlyphs">licensed and insured</text>
</svg>
</body>
</html>
```